Brimlow OrthoLink IT Inc. new website

i need a website for my company which is dedicated to installation and service of computer systems in Dental Offices. I would like for it to encompass a technology feel and professional look. The company deals with all aspects of technology like, Audio Visual, computer systems and networks, Cloud services like data backup, data center. We provide manage services, support and services to Dental Professionals.
Updates

Looking for a Technology font but professional look Added Wednesday, April 20, 2016

Target Market(s)

Dental, Dentist

Industry/Entity Type

Dental

Number of Pages Required

5+ page

Font styles to use
Other font styles liked:
• Futuristic or Techy

Colors
0255a3
ec1f27

Requirements
Must have
• Tabs
Nice to have
• Have no idea maybe some suggestion on your part may help
Should not have
• A professional feel but have a techy look

```html
<!DOCTYPE html>
<html lang="en">
<head>
<meta charset="utf-8">
<title>Brimlow OrthoLink IT Inc.</title>
<link rel="stylesheet" href="https://fonts.googleapis.com/css2?family=Raleway:wght@500;600;700;800;900&family=Open+Sans:wght@400;600;700&family=Lora:ital@1&display=swap">
<style>
:root{
  --blue:#0a56a5;
  --blue-dark:#08468a;
  --orange:#ef7d12;
  --ink:#222629;
  --text:#5f6366;
  --muted:#8a8e92;
  --soft:#e9edf2;
  --line:#dfe3e7;
  --footer:#272727;
  --footer-deep:#1b1b1b;
  --white:#ffffff;
}
*{box-sizing:border-box;margin:0;padding:0}
html,body{width:1200px;height:2462px;overflow:hidden}
body{position:relative;background:var(--white);font-family:"Open Sans",Arial,sans-serif;color:var(--text)}
.abs{position:absolute}
.heading{font-family:"Raleway",Arial,sans-serif;font-weight:800;color:var(--ink);letter-spacing:1.5px;text-transform:uppercase}
.script{font-family:"Lora",Georgia,serif;font-style:italic;color:var(--ink)}
.body-text{font-size:10.5px;line-height:17px;color:var(--text)}

/* header */
.site-header{top:0;left:0;width:1200px;height:61px;background:var(--white)}
.brand{left:243px;top:14px;font-family:"Raleway",sans-serif;font-weight:800;font-size:19px;color:var(--blue);display:flex;align-items:center;gap:8px}
.brand-mark{width:14px;height:14px;background:var(--blue);border-radius:2px}
.main-nav{left:565px;top:0;height:61px;display:flex}
.main-nav a{display:flex;align-items:center;padding:0 15px;height:61px;font-family:"Raleway",sans-serif;font-weight:600;font-size:10px;color:var(--ink);text-decoration:none;border-right:1px solid #eef0f2;text-transform:uppercase}
.main-nav a.active{background:var(--blue);color:var(--white);padding:0 17px}

/* hero */
.hero{top:61px;left:0;width:1200px;height:448px}
.hero-photo{width:100%;height:100%;background:linear-gradient(100deg,#6e7378 0%,#c9ccd0 22%,#e7e9ec 48%,#f3f4f6 62%,#dfe4ea 78%,#c9d6e6 100%)}
.hero-card{left:0;top:148px;width:594px;height:201px;background:rgba(255,255,255,.86)}
.hero-kicker{left:253px;top:180px;font-family:"Raleway",sans-serif;font-weight:700;font-size:11px;letter-spacing:1.5px;color:var(--ink)}
.hero-title{left:251px;top:194px;font-family:"Raleway",sans-serif;font-weight:900;font-size:30px;color:var(--ink);letter-spacing:.5px}
.hero-tag{left:253px;top:236px;font-family:"Raleway",sans-serif;font-weight:700;font-size:11px;line-height:15px;letter-spacing:.8px;color:var(--ink)}
.hero-contact{left:253px;top:282px;height:30px;width:307px;background:#0f0f0f;display:flex;font-family:"Raleway",sans-serif;font-weight:700;font-size:9px;color:var(--white);letter-spacing:.5px}
.hero-contact span{display:flex;align-items:center;gap:10px}
.ico-box{width:30px;height:30px;display:flex;align-items:center;justify-content:center}
.slider-dots{left:1167px;top:262px;display:flex;flex-direction:column;gap:5px}
.slider-dots i{width:9px;height:9px;border-radius:50%;background:#333;display:block}
.slider-dots i:first-child{background:#2f8fe0}

/* about */
.section-title{width:1200px;left:0;text-align:center;font-size:19px}
.section-sub{width:1200px;left:0;text-align:center;font-size:11px}
.about-copy{left:253px;width:694px;top:588px;text-align:center;font-size:10px;line-height:17px}
.btn-outline{display:flex;align-items:center;justify-content:center;font-family:"Raleway",sans-serif;font-weight:700;font-size:8.5px;letter-spacing:1px;text-transform:uppercase}
.read-more{left:550px;top:667px;width:92px;height:31px;border:1.5px solid var(--orange);color:var(--orange)}

/* services */
.services{top:720px;left:0;width:1200px;height:356px;background:var(--soft)}
.service{width:260px}
.service h3{font-family:"Raleway",sans-serif;font-weight:800;font-size:10px;letter-spacing:1px;color:var(--ink);text-transform:uppercase;position:relative;padding-top:4px;margin-bottom:6px}
.service h3::before{content:"";position:absolute;left:0;top:-5px;width:11px;height:2px;background:var(--blue)}
.service p{font-size:10px;line-height:17px}

/* testimonials */
.clients-title{left:253px;top:1134px;font-size:19px}
.clients-sub{left:253px;top:1159px;font-size:9px;color:var(--ink)}
.dot-row{display:flex;gap:4px}
.dot-row i{width:6px;height:6px;border-radius:50%;background:#2f8fe0;display:block}
.dot-row i:first-child{background:var(--orange)}
.testimonial{width:200px;top:1196px}
.quote-mark{position:absolute;left:0;top:-14px;font-family:Georgia,serif;font-size:96px;line-height:1;color:#e9eef4}
.testimonial p{position:relative;font-size:10px;line-height:17px}
.author{position:absolute;top:101px;left:0;display:flex;align-items:center;gap:24px;width:260px}
.avatar{width:40px;height:40px;border-radius:50%;background:linear-gradient(135deg,#b9a89b,#6b6560)}
.author b{display:block;font-family:"Raleway",sans-serif;font-weight:800;font-size:9px;letter-spacing:1px;color:var(--ink);text-transform:uppercase}
.author small{font-size:9px;color:var(--text)}

/* news */
.news{top:1384px;left:0;width:1200px;height:436px;background:var(--soft)}
.news-title{left:253px;top:1442px;font-size:19px}
.news-sub{left:253px;top:1466px;font-size:10px}
.date-col{left:253px;top:1502px;width:44px;text-align:center;font-size:8.5px;color:var(--text)}
.date-col .day{font-family:"Raleway",sans-serif;font-weight:800;font-size:19px;color:var(--ink);line-height:22px}
.date-col hr{border:0;border-top:1px solid #9aa0a6;margin:8px 0 10px}
.news-photo{left:312px;top:1507px;width:278px;height:133px;background:linear-gradient(120deg,#1f2f45,#3c6a9a 45%,#9db8d4 70%,#2b3f5a)}
.post h4{font-family:"Raleway",sans-serif;font-weight:800;font-size:10px;letter-spacing:1px;color:var(--ink);text-transform:uppercase}
.post .post-date{font-family:"Raleway",sans-serif;font-weight:700;font-size:7px;color:var(--orange);margin-top:4px;letter-spacing:.5px}
.post p{font-size:10px;line-height:18px;margin-top:8px}
.post-divider{left:621px;top:1593px;width:328px;height:1px;background:var(--line)}
.view-more{left:621px;top:1729px;width:92px;height:31px;border:1.5px solid var(--blue);color:var(--blue)}

/* partners */
.partner-row{left:253px;top:1937px;width:696px;height:78px;display:flex;border:1px solid var(--line)}
.partner{flex:1;border-right:1px solid var(--line);display:flex;align-items:center;justify-content:center}
.partner:last-child{border-right:0}
.partner span{width:50px;height:50px;border-radius:50%;background:#3a3a3a}
.partner span.sq{border-radius:4px;width:56px;height:34px}

/* call to action */
.cta{top:2083px;left:0;width:1200px;height:65px;background:var(--blue)}
.cta h2{position:absolute;left:253px;top:18px;font-family:"Raleway",sans-serif;font-weight:800;font-size:10.5px;color:var(--white);text-transform:uppercase;letter-spacing:.5px}
.cta p{position:absolute;left:253px;top:36px;font-size:9px;color:#d4e3f4}
.cta-btn{position:absolute;left:842px;top:19px;width:106px;height:29px;background:var(--orange);color:var(--white);font-family:"Raleway",sans-serif;font-weight:700;font-size:8.5px;display:flex;align-items:center;justify-content:center;text-transform:uppercase}

/* footer */
.site-footer{top:2148px;left:0;width:1200px;height:314px;background:var(--footer)}
.footer-head{font-family:"Raleway",sans-serif;font-weight:800;font-size:10px;color:var(--white);text-transform:uppercase;letter-spacing:.5px}
.link-list{width:98px;list-style:none}
.link-list li{font-family:"Raleway",sans-serif;font-weight:600;font-size:8px;color:#cfcfcf;text-transform:uppercase;height:26px;line-height:18px;border-bottom:1px solid #3d3d3d;margin-bottom:0}
.link-list li:last-child{border-bottom:0}
.footer-text{font-size:8.5px;line-height:15px;color:#bdbdbd}
.footer-text b{color:var(--white);font-family:"Raleway",sans-serif;font-weight:800;text-transform:uppercase;font-size:8.5px}
.newsletter-input{left:731px;top:2303px;width:182px;height:28px;background:#1c1c1c;font-size:8px;color:#9a9a9a;padding:9px 12px}
.newsletter-btn{left:913px;top:2303px;width:35px;height:28px;background:var(--blue);display:flex;align-items:center;justify-content:center}
.copyright{left:253px;top:2410px;font-size:8px;color:#9a9a9a}
.legal-bar{left:608px;top:2406px;width:592px;height:32px;background:var(--footer-deep);display:flex;align-items:center;gap:18px;padding-left:32px}
.legal-bar span{font-size:8px;color:#bdbdbd}
</style>
</head>
<body>

<header class="site-header abs">
  <div class="brand abs"><span class="brand-mark"></span>Brimlow OrthoLink IT</div>
  <nav class="main-nav abs">
    <a class="active">Home</a><a>About Us</a><a>Services</a><a>Blog</a><a>FAQ's</a><a>Contact Us</a>
  </nav>
</header>

<section class="hero abs">
  <div class="hero-photo" role="img" aria-label="Laptop with blue stethoscope on the left and a smiling professional in shirt and tie on the right"></div>
</section>
<div class="hero-card abs"></div>
<div class="hero-kicker abs">CONTACT TO</div>
<h1 class="hero-title abs">BRIMLOW ORTHOLINK IT</h1>
<p class="hero-tag abs">WE PROVIDE MANAGE SERVICES, SUPPORT AND<br>SERVICE TO DENTAL PROFESSIONALS.</p>
<div class="hero-contact abs">
  <span><span class="ico-box" style="background:var(--blue)"><svg width="13" height="13" viewBox="0 0 24 24"><path d="M6.6 10.8a15 15 0 006.6 6.6l2.2-2.2c.3-.3.7-.4 1-.2 1.1.4 2.3.6 3.6.6.6 0 1 .4 1 1V20c0 .6-.4 1-1 1A17 17 0 013 4c0-.6.4-1 1-1h3.5c.6 0 1 .4 1 1 0 1.3.2 2.5.6 3.6.1.3 0 .7-.2 1z" fill="none" stroke="#fff" stroke-width="1.8"/></svg></span>+1 555 204 7781</span>
  <span style="margin-left:18px"><span class="ico-box" style="background:var(--orange)"><svg width="14" height="12" viewBox="0 0 24 20"><path d="M2 8l10-6 10 6v10H2z M2 8l10 6 10-6" fill="none" stroke="#fff" stroke-width="1.8"/></svg></span>HELLO@BRIMLOWORTHOLINK.COM</span>
</div>
<div class="slider-dots abs"><i></i><i></i><i></i></div>

<!-- About -->
<h2 class="heading section-title abs" style="top:540px">About Us</h2>
<p class="script section-sub abs" style="top:564px">Our Short Story</p>
<p class="about-copy abs">Donec imperdiet rutrum cursus. Vivamus ut sodales lectus. Donec egestas ligula metus, ut eleifend metus pellentesque in. Nullam laoreet mattis aliquam. Class aptent taciti sociosqu ad litora torquent per conubia nostra, per inceptos himenaeos. Etiam aliquet, elit et tempus ultrices, felis nulla dapibus justo, sed dapibus mi orci ut diam. Cum sociis natoque penatibus et magnis dis parturient montes, nascetur ridiculus mus. Cras ut imperdiet augue. Nullam eget fringilla libero. Pellentesque scelerisque lectus lectus, nec maximus diam efficitur a.</p>
<div class="btn-outline read-more abs">Read More</div>

<!-- Services -->
<section class="services abs"></section>
<h2 class="heading section-title abs" style="top:774px">Services</h2>
<p class="section-sub abs" style="top:801px;font-size:9px;color:var(--ink)">What we are doing</p>

<svg class="abs" style="left:251px;top:851px" width="30" height="38" viewBox="0 0 30 38"><path d="M2 2h18l8 8v26H2z" fill="none" stroke="#0a56a5" stroke-width="2.4"/><path d="M20 2v8h8" fill="none" stroke="#0a56a5" stroke-width="2"/><path d="M8 18h4l5-4v14l-5-4H8z" fill="#0a56a5"/><path d="M20 17a5 5 0 010 8" fill="none" stroke="#0a56a5" stroke-width="1.8"/></svg>
<div class="service abs" style="left:317px;top:853px"><h3>Audio Visual</h3><p>Lorem Ipsum is simply dummy text of the printing and industry Lorem Ipsum has been the industry's standard dummy text.</p></div>

<svg class="abs" style="left:628px;top:856px" width="38" height="28" viewBox="0 0 38 28"><rect x="6" y="2" width="26" height="18" rx="1" fill="none" stroke="#0a56a5" stroke-width="2.4"/><path d="M1 24h36v2H1z" fill="#0a56a5"/></svg>
<div class="service abs" style="left:695px;top:853px"><h3>Computer Systems</h3><p>Lorem Ipsum is simply dummy text of the printing and industry Lorem Ipsum has been the industry's standard dummy text.</p></div>

<svg class="abs" style="left:251px;top:951px" width="36" height="34" viewBox="0 0 36 34"><g fill="#0a56a5"><rect x="13" y="0" width="10" height="9"/><rect x="0" y="24" width="10" height="9"/><rect x="13" y="24" width="10" height="9"/><rect x="26" y="24" width="10" height="9"/></g><path d="M18 9v8M5 24v-7h26v7M18 17v7" fill="none" stroke="#0a56a5" stroke-width="2"/></svg>
<div class="service abs" style="left:317px;top:950px"><h3>Computer Networks</h3><p>Lorem Ipsum is simply dummy text of the printing and industry Lorem Ipsum has been the industry's standard dummy text.</p></div>

<svg class="abs" style="left:628px;top:954px" width="40" height="26" viewBox="0 0 40 26"><path d="M10 26a9 9 0 010-18 12 12 0 0122 2 8 8 0 01-1 16z" fill="#0a56a5"/></svg>
<div class="service abs" style="left:695px;top:950px"><h3>Cloud Services of Data Backup</h3><p>Lorem Ipsum is simply dummy text of the printing and industry Lorem Ipsum has been the industry's standard dummy text.</p></div>

<!-- Testimonials -->
<h2 class="heading clients-title abs">Clients</h2>
<p class="clients-sub abs">Whats our client says</p>
<div class="dot-row abs" style="left:923px;top:1147px"><i></i><i></i><i></i></div>

<div class="testimonial abs" style="left:253px"><span class="quote-mark">“</span><p>Lorem Ipsum is simply dummy text of the printing and typesetting industry. Lorem Ipsum has been the industry's standard dummy text ever since the 1500s, when an unknown.</p>
  <div class="author"><span class="avatar" role="img" aria-label="Client portrait"></span><div><b>Tomas Reyner</b><small>Designation</small></div></div></div>
<div class="testimonial abs" style="left:491px"><span class="quote-mark">“</span><p>Lorem Ipsum is simply dummy text of the printing and typesetting industry. Lorem Ipsum has been the industry's standard dummy text ever since the 1500s, when an unknown.</p>
  <div class="author"><span class="avatar" role="img" aria-label="Client portrait"></span><div><b>Elena Varsk</b><small>Designation</small></div></div></div>
<div class="testimonial abs" style="left:727px"><span class="quote-mark" style="color:#f6e6d2">“</span><p>Lorem Ipsum is simply dummy text of the printing and typesetting industry. Lorem Ipsum has been the industry's standard dummy text ever since the 1500s, when an unknown.</p>
  <div class="author"><span class="avatar" role="img" aria-label="Client portrait"></span><div><b>Owen Maddox</b><small>Designation</small></div></div></div>

<!-- News -->
<section class="news abs"></section>
<h2 class="heading news-title abs">News</h2>
<p class="script news-sub abs">From Our Blog</p>
<div class="date-col abs">
  <div class="day">30</div>Oct-2015<hr>
  <svg width="16" height="14" viewBox="0 0 24 20"><path d="M3 3h18v11H9l-5 4v-4H3z" fill="none" stroke="#333" stroke-width="2"/></svg><div>8- Com</div>
  <hr style="border:0;margin:8px 0">
  <svg width="16" height="12" viewBox="0 0 24 16"><path d="M1 8s4-7 11-7 11 7 11 7-4 7-11 7S1 8 1 8z" fill="none" stroke="#333" stroke-width="2"/><circle cx="12" cy="8" r="3" fill="#333"/></svg><div>16- View</div>
</div>
<div class="news-photo abs" role="img" aria-label="Hand holding a tablet in front of a server room with glowing technology icons"></div>
<article class="post abs" style="left:312px;top:1661px;width:278px"><h4>Blog Heading</h4><p style="margin-top:6px">Lorem Ipsum is simply dummy text of the printing and typesetting industry. Lorem Ipsum has been the industry's standard dummy...</p></article>
<article class="post abs" style="left:621px;top:1503px;width:330px"><h4>Blog Heading</h4><div class="post-date">30 - OCT - 2015</div><p>Lorem Ipsum is simply dummy text of the printing and typesetting industry. Lorem Ipsum has been the industry's standard dummy...</p></article>
<div class="post-divider abs"></div>
<article class="post abs" style="left:621px;top:1614px;width:330px"><h4>Blog Heading</h4><div class="post-date">7 - OCT - 2015</div><p>Lorem Ipsum is simply dummy text of the printing and typesetting industry. Lorem Ipsum has been the industry's standard dummy text ever since the 1500s, when an unknown printer took a galley of type and scrambled...</p></article>
<div class="btn-outline view-more abs">View More</div>

<!-- Partners -->
<h2 class="heading section-title abs" style="top:1876px">Our Clients</h2>
<p class="section-sub abs" style="top:1901px;font-size:9px;color:var(--ink)">Lorem ipsum</p>
<div class="partner-row abs">
  <div class="partner"><span></span></div>
  <div class="partner"><span class="sq"></span></div>
  <div class="partner"><span></span></div>
  <div class="partner"><span class="sq"></span></div>
  <div class="partner"><span></span></div>
  <div class="partner"><span class="sq"></span></div>
</div>
<div class="dot-row abs" style="left:587px;top:2035px"><i></i><i></i><i></i></div>

<!-- CTA -->
<section class="cta abs">
  <h2>Lorem ipsum dolor sit amet, consectetur</h2>
  <p>Lorem ipsum dolor sit amet, consectetur adipiscing elit. Nunc consequat elementum tempor. Duis porta lectus ut dui consequat.</p>
  <div class="cta-btn">Contact Now</div>
</section>

<!-- Footer -->
<footer class="site-footer abs"></footer>
<h3 class="footer-head abs" style="left:256px;top:2205px">Quick Links</h3>
<ul class="link-list abs" style="left:256px;top:2256px"><li>Home</li><li>About Me</li><li>Services</li><li>Resources</li></ul>
<ul class="link-list abs" style="left:374px;top:2256px;width:100px"><li>FAQ</li><li>Privacy Policy</li><li>Contact</li></ul>

<h3 class="footer-head abs" style="left:504px;top:2205px">Contact Us</h3>
<div class="footer-text abs" style="left:504px;top:2254px;width:210px">
  <b>Harbor Lane Office</b><br>
  Contact Address will appear here, some text gonna appear here, Ney York City, - 10001, USA<br>
  <span style="display:block;height:13px"></span>
  <b style="text-transform:none;font-family:'Open Sans'">Phone :</b> 555 0188 240<br>
  <b style="text-transform:none;font-family:'Open Sans'">Email :</b> hello@brimlowortholink.com
</div>

<h3 class="footer-head abs" style="left:731px;top:2205px">Newsletter Signup</h3>
<p class="footer-text abs" style="left:731px;top:2255px;width:220px">If you want receive our all weekly updates about new offers and discount, signup below.</p>
<div class="newsletter-input abs">Email Address</div>
<div class="newsletter-btn abs"><svg width="13" height="13" viewBox="0 0 24 24"><path d="M2 11L22 2l-7 20-3-8z" fill="#fff"/></svg></div>

<p class="copyright abs">Copyright 2016 &nbsp;&nbsp; Your site All Rights Reserved</p>
<div class="legal-bar abs"><span>Terms of Use</span><span>Legal Desclaimer</span><span>Privacy Policy</span><span>Support</span><span>Sitemap</span></div>

</body>
</html>
```